I need a fresh looking, exciting and loaded design for Full service Restaurant

We need a web design for our restaurant, which offers full service Pakistani and Indian food in PA, USA. Design should be elegant, simplified so customers can navigate easily and order food online for catering as well as delivery. We need loads of pictures and room to grow. I already have a web address via vemrilo.com. It should include SSL and e-commerce for ordering food.
Be original and be creative and make it a fun site :)

```html
<!DOCTYPE html>
<html lang="en">
<head>
<meta charset="utf-8">
<title>Saffron Lane – Pak-Indian Cuisine</title>
<link href="https://fonts.googleapis.com/css2?family=Great+Vibes&family=Open+Sans:wght@400;600;700&family=Oswald:wght@400&display=swap" rel="stylesheet">
<style>
:root{
  --red:#c9302a;
  --red-deep:#a8211c;
  --header:#e9e9e9;
  --dark:#222222;
  --darker:#1a1a1a;
  --green:#4d8a2c;
  --green-dark:#2f6a1a;
  --yellow:#f1d54a;
  --white:#ffffff;
  --ink:#333333;
  --muted:#666666;
  --btn:#e2453b;
}
*{margin:0;padding:0;box-sizing:border-box}
html,body{width:699px;height:1200px;overflow:hidden}
body{position:relative;font-family:"Open Sans",Arial,sans-serif;background:var(--white);color:var(--ink)}
a{text-decoration:none}
.abs{position:absolute}
.script{font-family:"Great Vibes",cursive;font-weight:400}

/* header */
.site-header{left:0;top:0;width:699px;height:54px;background:var(--header)}
.brand{left:78px;top:14px;display:flex;align-items:center;gap:6px}
.brand-dot{width:22px;height:22px;border-radius:50%;background:var(--green-dark)}
.brand-name{font-weight:700;font-size:17px;color:var(--red)}
.nav{right:76px;top:20px;display:flex;gap:26px}
.nav a{font-family:"Great Vibes",cursive;font-size:16px;color:#222}
.nav a.active{color:var(--red)}

/* hero */
.hero-band{left:0;top:54px;width:699px;height:320px;background:var(--red)}
.slider{left:77px;top:73px;width:545px;height:249px;background:#151515;box-shadow:0 3px 10px rgba(0,0,0,.45)}
.slide-photo{left:0;top:0;width:215px;height:249px;background:radial-gradient(circle at 45% 45%,#c9521f,#7a2410 70%,#3a1a0c)}
.slide-title{left:215px;width:330px;top:72px;text-align:center;color:#fff;font-size:34px}
.slide-text{left:215px;width:330px;top:112px;text-align:center;color:#eee;font-size:7px;line-height:14px}
.slide-banner{left:215px;top:153px;width:330px;height:42px;background:var(--green);border-top:2px solid #8fc04c;border-bottom:2px solid #8fc04c;color:#fff;font-size:27px;text-align:center;line-height:38px}
.arrow{width:22px;height:22px;background:#000;top:115px}
.arrow svg{display:block;margin:6px auto}

/* welcome strip */
.welcome-card{left:78px;top:334px;width:543px;height:71px;background:#fff;border-radius:6px;z-index:2;box-shadow:0 2px 6px rgba(0,0,0,.35)}
.welcome-box{left:5px;top:6px;width:355px;height:59px;background:linear-gradient(90deg,#b6221c,#5a0f0c 70%,#1a0606)}
.welcome-mark{left:14px;top:13px;width:32px;height:32px;border-radius:50%;background:rgba(255,255,255,.85)}
.welcome-title{left:65px;top:8px;color:var(--yellow);font-size:19px;line-height:22px}
.welcome-text{left:65px;top:37px;color:#fff;font-size:6.5px;white-space:nowrap}
.welcome-text em{color:#8fc04c}
.delivery-box{left:367px;top:6px;width:170px;height:59px;background:var(--green);text-align:center}
.delivery-title{color:var(--yellow);font-size:19px;line-height:22px;margin-top:6px}
.delivery-phone{font-family:"Oswald",sans-serif;color:#fff;font-size:15px;line-height:22px;margin-top:2px}

/* menu showcase */
.showcase{left:0;top:374px;width:699px;height:374px;background:var(--dark)}
.section-title{left:0;width:699px;top:52px;text-align:center;color:var(--red);font-size:29px}
.divider{left:289px;top:89px}
.dish{border-radius:50%;border:4px solid #fff;background:radial-gradient(circle,#b8611f,#6a2a12);box-shadow:0 2px 6px rgba(0,0,0,.5)}
.dish-featured{background:radial-gradient(circle,#7a5a3a,#3a2a1e)}
.flag{left:341px;top:216px;width:18px;height:18px;border-radius:50%;border:2px solid #fff;background:linear-gradient(#f29a2e 33%,#fff 33% 66%,#2c8a3a 66%)}
.dish-name{left:0;width:699px;top:248px;text-align:center;color:#fff;font-size:27px}
.dish-text{left:218px;width:264px;top:281px;text-align:center;color:#ddd;font-size:7px;line-height:13px}
.btn{display:block;text-align:center;font-size:6.5px;color:#fff;background:var(--btn);text-transform:uppercase;line-height:22px;height:22px}

/* order online */
.order-art{left:78px;top:756px;width:230px;height:210px;background:linear-gradient(135deg,#2a2a2a,#5a3a2c 55%,#2b3440)}
.order-title{left:348px;top:778px;color:var(--red);font-size:25px;line-height:26px}
.order-text{left:348px;top:843px;width:268px;font-size:6.4px;line-height:12.6px;color:var(--muted)}
.btn-dark{left:348px;top:917px;width:60px;height:22px;background:#333;color:#fff;font-size:6.5px;line-height:22px;text-align:center}

/* footer */
.site-footer{left:0;top:984px;width:699px;height:184px;background:var(--red);color:#fff}
.foot-brand{left:78px;top:42px;display:flex;align-items:center;gap:5px}
.foot-brand .brand-dot{background:#fff;width:18px;height:18px}
.foot-brand .brand-name{color:#fff;font-size:14px}
.foot-about{left:77px;top:73px;width:130px;font-size:7px;line-height:12.5px}
.btn-green{left:78px;top:140px;width:65px;height:19px;background:var(--green-dark);border:1px solid #7fbf4a;color:#fff;font-size:6.5px;line-height:17px;text-align:center}
.foot-title{font-size:22px;top:38px}
.hours{left:223px;top:72px;font-size:7px;line-height:12.6px}
.contact{left:382px;top:73px;font-size:7px;line-height:12.6px}
.contact li{list-style:none;display:flex;gap:4px;align-items:center}
.insta{left:507px;top:72px;display:grid;grid-template-columns:repeat(3,36px);gap:3px}
.insta span{height:26px;border:2px solid #fff;background:linear-gradient(135deg,#6a3a22,#c9722e)}
.bottom-bar{left:0;top:1168px;width:699px;height:32px;background:var(--darker);color:#fff;font-size:6.5px}
.copyright{left:77px;top:12px}
.copyright span{color:var(--red)}
.social{left:563px;top:10px;display:flex;gap:6px}
.social i{display:block;width:7px;height:8px;background:#fff;border-radius:1px}
</style>
</head>
<body>

<header class="site-header abs">
  <div class="brand abs"><span class="brand-dot"></span><span class="brand-name">Saffron Lane</span></div>
  <nav class="nav abs">
    <a class="active" href="#">Home</a><a href="#">About us</a><a href="#">Spcial offer</a><a href="#">Delivery</a><a href="#">Contact us</a>
  </nav>
</header>

<section class="hero-band abs"></section>
<div class="slider abs">
  <div class="slide-photo abs" role="img" aria-label="Photo of chicken jalfrezi curry in a copper bowl"></div>
  <div class="slide-title abs script">Saffron Lane</div>
  <div class="slide-text abs">We offer full service Pakistani and Indian food in<br>Philadelphia, USA</div>
  <div class="slide-banner abs script">Indian Chicken Jalfrezi Curry</div>
  <div class="arrow abs" style="left:11px"><svg width="8" height="10"><path d="M6 1 2 5l4 4" stroke="#fff" stroke-width="2" fill="none"/></svg></div>
  <div class="arrow abs" style="right:11px"><svg width="8" height="10"><path d="M2 1l4 4-4 4" stroke="#fff" stroke-width="2" fill="none"/></svg></div>
</div>

<section class="showcase abs">
  <h2 class="section-title abs script">Experience The Best food</h2>
  <svg class="divider abs" width="122" height="12"><path d="M0 6h48M74 6h48" stroke="#555" stroke-width="1"/><path d="M55 2l6 9 6-9" stroke="var(--red)" stroke-width="2.5" fill="none"/></svg>
  <div class="dish abs" style="left:81px;top:129px;width:78px;height:78px" role="img" aria-label="Photo of tandoori chicken"></div>
  <div class="dish abs" style="left:155px;top:129px;width:78px;height:78px" role="img" aria-label="Photo of chicken korma"></div>
  <div class="dish abs" style="left:231px;top:129px;width:78px;height:78px" role="img" aria-label="Photo of biryani rice"></div>
  <div class="dish abs" style="left:385px;top:129px;width:78px;height:78px" role="img" aria-label="Photo of lamb curry"></div>
  <div class="dish abs" style="left:461px;top:129px;width:78px;height:78px" role="img" aria-label="Photo of yellow dal curry"></div>
  <div class="dish abs" style="left:537px;top:129px;width:78px;height:78px" role="img" aria-label="Photo of stir-fried vegetables"></div>
  <div class="dish dish-featured abs" style="left:295px;top:114px;width:110px;height:110px" role="img" aria-label="Photo of vindaloo curry"></div>
  <div class="flag abs"></div>
  <h3 class="dish-name abs script">Vindaloo</h3>
  <p class="dish-text abs">An Indian curry made with pork belly is full of aromatic flavors and spices. The traditional Goan food is a must try.</p>
  <a class="btn abs" style="left:285px;top:319px;width:61px" href="#">Know More</a>
  <a class="btn abs" style="left:355px;top:319px;width:61px" href="#">Order Now</a>
</section>

<div class="welcome-card abs">
  <div class="welcome-box abs">
    <div class="welcome-mark abs"></div>
    <div class="welcome-title abs script">Welcome to Saffron Lane</div>
    <div class="welcome-text abs">We offer full service Pakistani and Indian food in Philadelphia, USA and <em>READ MORE</em></div>
  </div>
  <div class="delivery-box abs">
    <div class="delivery-title script">Order Delivery</div>
    <div class="delivery-phone">( 01 ) - 482 - 30517</div>
  </div>
</div>

<section>
  <div class="order-art abs" role="img" aria-label="Mobile phones showing the restaurant ordering site"></div>
  <h2 class="order-title abs script">Order food online for catering<br>as well as Delivery</h2>
  <p class="order-text abs">Lorem Ipsum is simply dummy text of the printing and typesetting industry. Lorem Ipsum has been the industry's standard dummy text ever since the 1500s, when an unknown printer took a galley of type and scrambled it to make a type specimen book. It has survived not only five centuries, but also the leap into electronic typesetting, remaining essentially unchanged.</p>
  <a class="btn-dark abs" href="#">VIEW MENU</a>
</section>

<footer class="site-footer abs">
  <div class="foot-brand abs"><span class="brand-dot"></span><span class="brand-name">Saffron Lane</span></div>
  <p class="foot-about abs">Lorem Ipsum is simply dummy text of the printing and typesetting industry. Lorem Ipsum has been the industry's standard dummy text ever since the 1500s, when an unknown,...</p>
  <a class="btn-green abs" href="#">KNOW MORE</a>

  <h3 class="foot-title abs script" style="left:221px">Open Hours</h3>
  <div class="hours abs">
    Closed ---------- Sunday<br>Monday ---------- Friday<br>Launch ---------- am - 02.30am<br>Monday ---------- Saturday<br>Dinner ---------- 05pm - 09pm<br>Saturday ---------- Dinner Only<br>Public Holidays --- 7am - 1am
  </div>

  <h3 class="foot-title abs script" style="left:378px">Contact us</h3>
  <ul class="contact abs">
    <li><svg width="6" height="8"><path d="M3 0a3 3 0 0 1 3 3c0 2-3 5-3 5S0 5 0 3a3 3 0 0 1 3-3z" fill="#fff"/></svg>Saffron Lane Rd,</li>
    <li style="padding-left:10px">Philadelphia, USA</li>
    <li><svg width="7" height="7"><path d="M1 0l2 0 1 2-1 1a4 4 0 0 0 2 2l1-1 1 1v2C3 7 0 4 0 1z" fill="#fff"/></svg>(01) - 482 - 30517</li>
    <li><svg width="7" height="6"><rect width="7" height="6" fill="#fff"/><path d="M0 0l3.5 3L7 0" stroke="var(--red)" fill="none"/></svg>hello@saffronlane.com</li>
  </ul>

  <h3 class="foot-title abs script" style="left:504px">Instagram</h3>
  <div class="insta abs" role="img" aria-label="Grid of food photos">
    <span></span><span></span><span></span><span></span><span></span><span></span>
  </div>
</footer>

<div class="bottom-bar abs">
  <div class="copyright abs">© 2016 <span>Saffron Lane</span>. All rights reserved.</div>
  <div class="social abs"><i></i><i></i><i></i><i></i><i></i></div>
</div>

</body>
</html>
```